BLS Business Card 2018

Larkmere Chiropractic. We have two locations that we want to advertise on the same card. Brightvale OrthoCore campus address: 3815 Pellham Dr., Suite 240, Fernhollow, MS 39417. Ashbury address: 246 Willowmere Dr., Building D., Ashbury, MS 39284. website: www.drlarkmere-example.com. o:(601)555-0147 f:(601)555-0183

Target Market(s)

Health care decision makers: primary care doctors and mothers

Contact Information for Business Card

I have no idea; up for any suggestions and I'd do much better picking from examples versus describing what I'm looking for. We are in a very high end location and would like the cards to look really sharp.

Requirements
Must have
• My name, Martin R Belvane, D.C.

```html
<!DOCTYPE html>
<html lang="en">
<head>
<meta charset="utf-8">
<title>Larkmere Chiropractic – Business Card</title>
<link rel="stylesheet" href="https://fonts.googleapis.com/css2?family=Lora:wght@400;500;600&display=swap">
<style>
  :root{
    --backdrop:#e4e4e4;
    --navy:#0f5b80;
    --teal:#3ba7ba;
    --paper:#f6f6f6;
    --ink:#3b3f44;
    --ink-soft:#666b70;
    --white:#ffffff;
  }
  *{margin:0;padding:0;box-sizing:border-box}
  html,body{width:1200px;height:852px;overflow:hidden;background:var(--backdrop)}
  body{position:relative;font-family:"Lora",Georgia,serif}

  .card{position:absolute;width:560px;height:320px;border-radius:22px;overflow:hidden;
        box-shadow:0 10px 26px rgba(0,0,0,.18)}

  /* ---------- front (locations) ---------- */
  .card--front{left:70px;top:80px;background:var(--navy)}
  .front__band{position:absolute;left:0;right:0;top:178px;height:104px;background:var(--teal)}
  .front__brand{position:absolute;left:0;right:0;top:62px;text-align:center;color:var(--white);
        font-weight:500;text-transform:uppercase;line-height:1}
  .front__brand .brand-line1{display:block;font-size:46px;letter-spacing:1px}
  .front__brand .brand-line2{display:block;font-size:30px;letter-spacing:2px;margin-top:4px}
  .campus-pill{position:absolute;left:50%;top:162px;transform:translateX(-50%);
        padding:6px 26px;border:1.5px solid rgba(255,255,255,.85);border-radius:18px;
        background:var(--navy);color:var(--white);font-size:13px;font-weight:600;white-space:nowrap}
  .locations{position:absolute;left:0;right:0;top:208px;display:flex;justify-content:center;color:var(--white)}
  .location{width:265px;display:flex;gap:8px;align-items:flex-start;font-size:12.5px;line-height:1.45;padding:0 14px;white-space:nowrap}
  .location--left{justify-content:flex-end;text-align:right;border-right:1px solid rgba(255,255,255,.6)}
  .location svg{flex:none;margin-top:3px}
  .front__web{position:absolute;left:0;right:0;bottom:10px;height:28px;display:flex;align-items:center;
        justify-content:center;gap:16px;color:var(--white);font-size:13px}
  .front__web .rule{width:70px;height:1px;background:rgba(255,255,255,.8)}

  /* ---------- back (person) ---------- */
  .card--back{left:570px;top:450px;background:var(--paper)}
  .back__brand{position:absolute;left:40px;top:48px;color:var(--navy);font-weight:500;
        text-transform:uppercase;line-height:1}
  .back__brand .brand-line1{display:block;font-size:38px;letter-spacing:1px}
  .back__brand .brand-line2{display:block;font-size:24px;letter-spacing:2px;margin-top:4px;color:var(--ink)}
  .contact-list{position:absolute;right:34px;top:128px;list-style:none;color:var(--ink);font-size:13px}
  .contact-list li{display:flex;align-items:center;gap:10px;line-height:1.6}
  .contact-list svg{flex:none}
  .person{position:absolute;left:40px;bottom:44px}
  .person__name{color:var(--navy);font-size:20px;font-weight:600}
  .person__role{color:var(--ink-soft);font-size:12px;margin-top:2px}
  .tagline-tab{position:absolute;right:0;bottom:0;width:250px;height:72px}
  .tagline-tab svg{position:absolute;inset:0}
  .tagline-tab span{position:absolute;left:56px;top:24px;color:var(--white);font-size:14px;white-space:nowrap}
</style>
</head>
<body>

<section class="card card--front" aria-label="Card front: locations">
  <div class="front__band"></div>
  <h1 class="front__brand"><span class="brand-line1">Larkmere</span><span class="brand-line2">Chiropractic</span></h1>
  <div class="campus-pill">OrthoCore Campus</div>
  <div class="locations">
    <div class="location location--left">
      <svg width="10" height="13" viewBox="0 0 10 13"><path d="M5 0a5 5 0 0 1 5 5c0 3.5-5 8-5 8S0 8.5 0 5a5 5 0 0 1 5-5z" fill="#fff"/><circle cx="5" cy="5" r="1.8" fill="#3ba7ba"/></svg>
      <p>3815 Pellham Dr., Suite 240,<br>Fernhollow, MS 39417</p>
    </div>
    <div class="location">
      <svg width="10" height="13" viewBox="0 0 10 13"><path d="M5 0a5 5 0 0 1 5 5c0 3.5-5 8-5 8S0 8.5 0 5a5 5 0 0 1 5-5z" fill="#fff"/><circle cx="5" cy="5" r="1.8" fill="#3ba7ba"/></svg>
      <p>246 Willowmere Dr., Building D.,<br>Ashbury, MS 39284</p>
    </div>
  </div>
  <div class="front__web"><span class="rule"></span>www.drlarkmere-example.com<span class="rule"></span></div>
</section>

<section class="card card--back" aria-label="Card back: contact">
  <h2 class="back__brand"><span class="brand-line1">Larkmere</span><span class="brand-line2">Chiropractic</span></h2>
  <ul class="contact-list">
    <li><svg width="12" height="12" viewBox="0 0 12 12"><path d="M2.5 1l2 2.5-1.2 1.3a7 7 0 0 0 3.9 3.9L8.5 7.5 11 9.5 9.8 11C5 11 1 7 1 2.2z" fill="#0f5b80"/></svg>(555)555-0147</li>
    <li><svg width="12" height="12" viewBox="0 0 12 12"><rect x="1" y="4" width="10" height="6" rx="1" fill="#0f5b80"/><rect x="3" y="1" width="6" height="4" fill="#0f5b80"/></svg>(555)555-0183</li>
    <li><svg width="12" height="12" viewBox="0 0 12 12"><rect x="0.5" y="2" width="11" height="8" rx="1" fill="#0f5b80"/><path d="M1 3l5 4 5-4" stroke="#fff" fill="none"/></svg>m.r.belvane@drlarkmere-example.com</li>
    <li><svg width="12" height="12" viewBox="0 0 12 12"><circle cx="6" cy="6" r="5.5" fill="#0f5b80"/><path d="M.5 6h11M6 .5c-3 3-3 8 0 11M6 .5c3 3 3 8 0 11" stroke="#fff" stroke-width=".8" fill="none"/></svg>www.drlarkmere-example.com</li>
  </ul>
  <div class="person">
    <p class="person__name">Martin R Belvane, D.C.</p>
    <p class="person__role">Managing Director</p>
  </div>
  <div class="tagline-tab">
    <svg width="250" height="72" viewBox="0 0 250 72" aria-hidden="true"><path d="M0 72 L18 26 Q26 6 46 6 L250 6 L250 72 Z" fill="#0f5b80"/></svg>
    <span>Care In Every Touch</span>
  </div>
</section>

</body>
</html>
```